SkyvornQ Business Cards and Stationary Design

Need a design for our business cards and stationary. I want to carry on the theme of the logo. I want the business cards to have a design on the back. I would like the business cards and the stationary to carry the same theme, design scheme, and branding

Target Market(s)

Airlines and Maintenance Facilities

Industry/Entity Type

Aviation

Contact Information for Business Card

Name
Position Title
Address: 4827 Trellis Hollow Road, Fort Pierce, Florida, 34951
Office Number
Mobile Number
Email
Website

Font styles to use
Serif
Sans Serif

Colors

Designer to choose colors to be used in the design.

```html
<!DOCTYPE html>
<html lang="en">
<head>
<meta charset="utf-8">
<title>SkyvornQ Business Cards</title>
<link rel="stylesheet" href="https://fonts.googleapis.com/css2?family=Montserrat:wght@800&family=Saira+Semi+Condensed:wght@300;600&family=Source+Sans+3:wght@400&display=swap">
<style>
  :root {
    --backdrop-light: #e6e7e8;
    --backdrop-dark: #d3d4d6;
    --card: #ffffff;
    --card-edge: #2b2b2b;
    --navy: #1d3262;
    --sky: #25a1db;
    --grey-text: #555a60;
    --white: #ffffff;
  }
  * { margin: 0; padding: 0; box-sizing: border-box; }
  html, body { width: 1200px; height: 1104px; overflow: hidden; }
  body {
    position: relative;
    background: linear-gradient(135deg, var(--backdrop-light), var(--backdrop-dark));
    font-family: "Source Sans 3", sans-serif;
  }
  .card {
    position: absolute;
    width: 764px;
    height: 436px;
    background: var(--card);
    border: 1px solid var(--card-edge);
    border-radius: 24px;
    overflow: hidden;
  }
  .card--front { left: 67px; top: 79px; }
  .card--back { left: 342px; top: 574px; }

  .brand-ring { position: absolute; }
  .card--front .brand-ring { left: 176px; top: 46px; }
  .card--back .brand-ring { left: 56px; top: 62px; }

  .wordmark {
    position: absolute;
    font-family: "Montserrat", sans-serif;
    font-weight: 800;
    color: var(--navy);
    letter-spacing: 7px;
    line-height: 1;
    white-space: nowrap;
  }
  .card--front .wordmark { left: 54px; top: 193px; font-size: 41px; }
  .card--back .wordmark { left: 413px; top: 180px; font-size: 40px; letter-spacing: 6px; }

  .person {
    position: absolute;
    right: 30px;
    top: 62px;
    text-align: right;
    font-family: "Saira Semi Condensed", sans-serif;
    line-height: 1;
  }
  .person__name { font-weight: 600; font-size: 28px; color: var(--navy); }
  .person__title { font-weight: 300; font-size: 25px; color: var(--grey-text); margin-top: 8px; }

  .contact-band {
    position: absolute;
    left: 0; right: 0;
    top: 277px; bottom: 0;
    background: linear-gradient(90deg, var(--navy), var(--sky));
  }
  .contact-list {
    position: absolute;
    left: 54px;
    top: 36px;
    list-style: none;
    color: var(--white);
    font-size: 18px;
  }
  .contact-list li {
    display: flex;
    align-items: center;
    gap: 6px;
    height: 22px;
    margin-bottom: 10px;
  }
  .contact-list li.address { margin-top: 20px; }
  .contact-list .pair { margin-left: 10px; display: flex; align-items: center; gap: 6px; }
  .icon { width: 17px; height: 17px; flex: none; }

  .web {
    position: absolute;
    left: 413px;
    width: 330px;
    top: 232px;
    text-align: center;
    font-size: 19px;
    letter-spacing: 4.5px;
    color: var(--grey-text);
  }
</style>
</head>
<body>

<section class="card card--front" aria-label="Business card front">
  <svg class="brand-ring" width="118" height="118" viewBox="0 0 118 118" aria-hidden="true">
    <circle cx="59" cy="59" r="53" fill="none" stroke="var(--navy)" stroke-width="9"/>
  </svg>
  <div class="wordmark">SKYVORNQ</div>

  <div class="person">
    <div class="person__name">DORIAN PELLACOTT</div>
    <div class="person__title">PRESIDENT</div>
  </div>

  <div class="contact-band">
    <ul class="contact-list">
      <li>
        <svg class="icon" viewBox="0 0 18 18" aria-hidden="true"><circle cx="9" cy="9" r="7.8" fill="none" stroke="#fff" stroke-width="1.4"/><path d="M6 5.2l1.6-.4.9 2-1 .8a5 5 0 0 0 2.6 2.6l.8-1 2 .9-.4 1.6c-3.4.4-6.9-3.1-6.5-6.5z" fill="#fff"/></svg>
        012-345-6789
        <span class="pair">
          <svg class="icon" viewBox="0 0 18 18" aria-hidden="true"><circle cx="9" cy="9" r="7.8" fill="none" stroke="#fff" stroke-width="1.4"/><rect x="6.5" y="4.5" width="5" height="9" rx="1" fill="none" stroke="#fff" stroke-width="1.2"/></svg>
          012-345-6789
        </span>
      </li>
      <li>
        <svg class="icon" viewBox="0 0 18 18" aria-hidden="true"><circle cx="9" cy="9" r="7.8" fill="none" stroke="#fff" stroke-width="1.4"/><rect x="5" y="6" width="8" height="6" fill="none" stroke="#fff" stroke-width="1.2"/><path d="M5 6l4 3 4-3" fill="none" stroke="#fff" stroke-width="1.2"/></svg>
        info@skyvornq.com
        <span class="pair">
          <svg class="icon" viewBox="0 0 18 18" aria-hidden="true"><circle cx="9" cy="9" r="7.5" fill="none" stroke="#fff" stroke-width="1.3"/><ellipse cx="9" cy="9" rx="3.2" ry="7.5" fill="none" stroke="#fff" stroke-width="1.1"/><path d="M1.5 9h15M3 5h12M3 13h12" stroke="#fff" stroke-width="1.1"/></svg>
          www.skyvornq.com
        </span>
      </li>
      <li class="address">
        <svg class="icon" viewBox="0 0 18 18" aria-hidden="true"><circle cx="9" cy="9" r="7.8" fill="none" stroke="#fff" stroke-width="1.4"/><path d="M9 14s-3.2-3.6-3.2-6A3.2 3.2 0 0 1 12.2 8c0 2.4-3.2 6-3.2 6z" fill="#fff"/><circle cx="9" cy="8" r="1.2" fill="var(--navy)"/></svg>
        4827 Trellis Hollow Road, Fort Pierce, Florida, 34951
      </li>
    </ul>
  </div>
</section>

<section class="card card--back" aria-label="Business card back">
  <svg class="brand-ring" width="320" height="320" viewBox="0 0 320 320" aria-hidden="true">
    <circle cx="160" cy="160" r="147" fill="none" stroke="var(--navy)" stroke-width="24"/>
  </svg>
  <div class="wordmark">SKYVORNQ</div>
  <div class="web">www.skyvornq.com</div>
</section>

</body>
</html>
```